Wholesale in Gold Jewellery & Gold Bullion

We are an established gold jewellery and gold bullion wholesaler selling these products to international clients. We already have a name and logo of our company, hence please view attached current card design. We need a completely new design to compliment our business and industry and the final design should be new and elegant.

Contact Information for Business Card

New card details must be same as per current card. Like logo, name, tel no. & etc.

Colors

Designer to choose colors to be used in the design.

```html
<!DOCTYPE html>
<html lang="en">
<head>
<meta charset="UTF-8">
<title>Vardan &amp; Co — Business Card</title>
<link rel="stylesheet" href="https://fonts.googleapis.com/css2?family=Libre+Baskerville:wght@700&family=Montserrat:wght@400;600&display=swap">
<style>
  :root {
    --page-bg: #d9d9d9;
    --card-bg: #f6f6f5;
    --gold: #c08a1e;
    --ink: #111111;
    --text: #2a2a2a;
  }
  * { box-sizing: border-box; margin: 0; padding: 0; }
  html, body {
    width: 1200px;
    height: 900px;
    overflow: hidden;
    background: var(--page-bg);
  }
  .card {
    position: absolute;
    left: 100px;
    top: 164px;
    width: 1000px;
    height: 571px;
    background: var(--card-bg);
    box-shadow: 0 6px 24px rgba(0,0,0,0.18);
    font-family: "Montserrat", sans-serif;
    color: var(--text);
  }
  .brand {
    position: absolute;
    left: 64px;
    top: 92px;
    display: flex;
    align-items: center;
    gap: 30px;
  }
  .brand-mark {
    width: 96px;
    height: 96px;
    border-radius: 50%;
    border: 14px solid var(--gold);
  }
  .brand-name {
    font-family: "Libre Baskerville", serif;
    font-weight: 700;
    font-size: 29px;
    letter-spacing: 0.5px;
    color: var(--ink);
    margin-top: -36px;
  }
  .divider {
    position: absolute;
    left: 60px;
    top: 302px;
    width: 712px;
    height: 3px;
    background: var(--gold);
  }
  .person-name {
    position: absolute;
    right: 190px;
    top: 248px;
    font-weight: 600;
    font-size: 34px;
    color: var(--gold);
    letter-spacing: 0.3px;
  }
  .person-title {
    position: absolute;
    left: 782px;
    top: 290px;
    font-size: 23px;
    color: var(--text);
  }
  .address {
    position: absolute;
    right: 54px;
    top: 388px;
    text-align: right;
    font-size: 18px;
    line-height: 1.45;
    color: var(--text);
  }
  .contacts {
    position: absolute;
    left: 60px;
    top: 322px;
    list-style: none;
  }
  .contact-item {
    display: flex;
    align-items: center;
    gap: 22px;
    height: 38px;
    font-size: 23px;
    color: var(--text);
    letter-spacing: 0.3px;
  }
  .contact-icon {
    width: 24px;
    height: 24px;
    flex: none;
  }
</style>
</head>
<body>
  <section class="card">
    <div class="brand">
      <span class="brand-mark"></span>
      <span class="brand-name">VARDAN &amp; CO PTE LTD</span>
    </div>

    <div class="person-name">Rohan Meharvati</div>
    <div class="divider"></div>
    <div class="person-title">Director</div>

    <ul class="contacts">
      <li class="contact-item">
        <svg class="contact-icon" viewBox="0 0 24 24" aria-hidden="true">
          <rect x="6" y="2" width="12" height="20" rx="2" fill="none" stroke="var(--gold)" stroke-width="2"/>
          <line x1="10" y1="18.5" x2="14" y2="18.5" stroke="var(--gold)" stroke-width="1.6"/>
        </svg>
        <span>+65 9120 4438</span>
      </li>
      <li class="contact-item">
        <svg class="contact-icon" viewBox="0 0 24 24" aria-hidden="true">
          <path d="M7 3 L10 7 L8 9.5 C9 12 11.5 14.8 14.5 16 L17 14 L21 17 L19 21 C11 21 3 13 3 5 Z" fill="var(--gold)"/>
        </svg>
        <span>+65 6815 2200</span>
      </li>
      <li class="contact-item">
        <svg class="contact-icon" viewBox="0 0 24 24" aria-hidden="true">
          <rect x="6" y="2" width="12" height="9" fill="none" stroke="var(--gold)" stroke-width="1.8"/>
          <line x1="8.5" y1="5" x2="15.5" y2="5" stroke="var(--gold)" stroke-width="1.2"/>
          <line x1="8.5" y1="8" x2="15.5" y2="8" stroke="var(--gold)" stroke-width="1.2"/>
          <rect x="2" y="11" width="20" height="10" rx="1.5" fill="var(--gold)"/>
          <rect x="6" y="14" width="12" height="3" fill="var(--card-bg)"/>
        </svg>
        <span>+65 6407 5519</span>
      </li>
      <li class="contact-item">
        <svg class="contact-icon" viewBox="0 0 24 24" aria-hidden="true">
          <rect x="2" y="5" width="20" height="14" fill="var(--gold)"/>
          <path d="M2 5 L12 13 L22 5" fill="none" stroke="var(--card-bg)" stroke-width="1.6"/>
        </svg>
        <span>rohan@vardanco.com</span>
      </li>
    </ul>

    <address class="address" style="font-style: normal;">
      12 Lorin Quay Rd,<br>
      Singapore 408816
    </address>
  </section>
</body>
</html>
```